plumbers buisness card

A buisness card for a plumbing buisness
needs to have a water theme with navy blue, light blue and white
with an image of either a water drop, pipes, tools or something relating to plumbing and incorperating my buisness name as a logo

"Kettering Plumbing" is the words that need to stand out with "& gasfitting" to be smaller

spelling error on brief, "maintenance"
and also could you include my email d_kettering@mailwave.com.au

Industry/Entity Type

Plumbing

Contact Information for Business Card

Kettering Plumbing & Gasfitting

declan kettering
0432961085

specialising in
-new homes
-maitenance
-renovations

license no.
-73840

```html
<!DOCTYPE html>
<html lang="en">
<head>
<meta charset="utf-8">
<title>Kettering Plumbing &amp; Gasfitting – Business Card</title>
<link rel="stylesheet" href="https://fonts.googleapis.com/css2?family=Source+Sans+3:wght@400;600;700&display=swap">
<style>
  :root {
    --board-pink: #f09ac0;
    --label-ink: #1a1a1a;
    --navy: #1c2f5a;
    --band-white: #ffffff;
    --back-blue: #d6e4f2;
    --water-light: #eef5fb;
    --water-mid: #bcd6ec;
    --water-deep: #7fa9d1;
  }
  * { margin: 0; padding: 0; box-sizing: border-box; }
  html, body {
    width: 1200px;
    height: 426px;
    overflow: hidden;
    background: var(--board-pink);
    font-family: "Source Sans 3", "Myriad Pro", sans-serif;
    color: var(--navy);
  }
  .board { position: relative; width: 1200px; height: 426px; }

  .side-label {
    position: absolute;
    top: 16px;
    font-size: 31px;
    font-weight: 400;
    color: var(--label-ink);
    transform: translateX(-50%);
  }
  .side-label--front { left: 301px; }
  .side-label--back { left: 880px; }

  .card {
    position: absolute;
    top: 69px;
    width: 536px;
    height: 306px;
    overflow: hidden;
  }
  .card--front { left: 42px; }
  .card--back { left: 623px; background: var(--back-blue); }

  .card__photo {
    position: absolute;
    inset: 0;
    background:
      radial-gradient(ellipse 140px 100px at 305px 78px, var(--water-deep) 0%, var(--water-mid) 50%, transparent 78%),
      radial-gradient(ellipse 240px 110px at 110px 210px, var(--water-mid) 0%, transparent 72%),
      radial-gradient(ellipse 160px 80px at 470px 200px, var(--water-mid) 0%, transparent 70%),
      linear-gradient(135deg, var(--water-light) 0%, #dceaf6 50%, var(--water-light) 100%);
  }

  .logo-oval {
    position: absolute;
    left: 198px;
    top: 8px;
    width: 210px;
    height: 138px;
    border-radius: 50%;
    background: var(--band-white);
    box-shadow: 0 0 0 4px var(--water-mid);
    display: flex;
    flex-direction: column;
    align-items: center;
    justify-content: center;
    text-align: center;
  }
  .logo-oval .brand-name { font-size: 21px; font-weight: 700; line-height: 1.1; }
  .logo-oval .brand-tagline { font-size: 15px; font-weight: 400; line-height: 1.25; }

  .contact-line {
    position: absolute;
    left: 0;
    width: 100%;
    text-align: center;
    font-size: 13px;
  }
  .contact-line strong { font-weight: 700; }
  .card--front .contact-name { top: 199px; font-weight: 700; }
  .card--front .contact-email { top: 274px; }

  .band {
    position: absolute;
    left: 0;
    top: 230px;
    width: 100%;
    height: 26px;
    background: var(--band-white);
    display: flex;
    align-items: center;
    justify-content: center;
    font-size: 13px;
  }
  .band strong { font-weight: 700; }

  .back-title {
    position: absolute;
    top: 74px;
    width: 100%;
    text-align: center;
  }
  .back-title .brand-name { display: block; font-size: 36px; font-weight: 700; line-height: 1.1; }
  .back-title .brand-tagline { display: block; font-size: 27px; font-weight: 400; line-height: 1.3; }
</style>
</head>
<body>
<div class="board">
  <div class="side-label side-label--front">Front</div>
  <div class="side-label side-label--back">Back</div>

  <section class="card card--front">
    <div class="card__photo" role="img" aria-label="Soft blue close-up photograph of a chrome tap fitting with water"></div>
    <div class="logo-oval">
      <span class="brand-name">Kettering Plumbing</span>
      <span class="brand-tagline">&amp; gasfitting</span>
    </div>
    <p class="contact-line contact-name">Declan Kettering&nbsp; : &nbsp;0432961085</p>
    <p class="band"><strong>Specialising in</strong>&nbsp;:&nbsp; new homes &nbsp;- maintenance - renovations</p>
    <p class="contact-line contact-email"><strong>e-mail :</strong> d_kettering@mailwave.com.au | <strong>license no.</strong> 73840</p>
  </section>

  <section class="card card--back">
    <div class="back-title">
      <span class="brand-name">Kettering Plumbing</span>
      <span class="brand-tagline">&amp; gasfitting</span>
    </div>
    <p class="band"><strong>Declan Kettering&nbsp; : &nbsp;0432961085</strong></p>
  </section>
</div>
</body>
</html>
```